Newsletter Ad

I am looking for someone to design an advertisement for a mother's club newsletter. 4" wide X by 5" tall (and 2.5" wide X 5" tall if possible).

I'm a psychotherapist, so want the ad to look professional, but modern. I have a logo with my photo attached that can be incorporated into the design. The colors of my website are turquoise and white. I'd like to keep with that theme...so maybe some turquoise blocking to match the logo font color.

I'm uploading a logo as well as an ad draft with the content I'd like listed in the ad.

```html
<!DOCTYPE html>
<html lang="en">
<head>
<meta charset="utf-8">
<title>Dana Morrow, MA, MFT – Psychotherapy</title>
<link rel="stylesheet" href="https://fonts.googleapis.com/css2?family=Didact+Gothic&family=Nunito+Sans:wght@300;400&display=swap">
<style>
  :root {
    --teal: #379a98;
    --teal-title: #3a9c9a;
    --grey-rule: #8a8a8a;
    --grey-text: #777777;
    --ink: #1a1a1a;
    --white: #ffffff;
    --photo-top: #d9c7b8;
    --photo-bottom: #5b4636;
  }
  * { margin: 0; padding: 0; box-sizing: border-box; }
  html, body { width: 961px; height: 1200px; overflow: hidden; background: var(--white); }
  .ad {
    position: relative;
    width: 961px;
    height: 1200px;
    background: var(--white);
    font-family: "Didact Gothic", sans-serif;
    overflow: hidden;
  }
  .portrait {
    position: absolute;
    left: 0; top: 0;
    width: 222px; height: 358px;
    background: linear-gradient(180deg, var(--photo-top) 0%, #a88a72 45%, var(--photo-bottom) 100%);
  }
  .masthead__name {
    position: absolute;
    left: 232px; width: 590px; top: 106px;
    text-align: center;
    white-space: nowrap;
    font-family: "Nunito Sans", sans-serif;
    font-weight: 300;
    font-size: 45px;
    letter-spacing: 0;
    line-height: 1;
    color: var(--teal-title);
  }
  .masthead__rule {
    position: absolute;
    left: 242px; top: 177px;
    width: 566px; height: 2px;
    background: var(--grey-rule);
  }
  .masthead__service {
    position: absolute;
    left: 242px; width: 574px; top: 200px;
    text-align: center;
    white-space: nowrap;
    font-family: "Nunito Sans", sans-serif;
    font-weight: 400;
    font-size: 56px;
    line-height: 1;
    color: var(--grey-text);
  }
  .masthead__service small { font-size: 28px; margin-left: 6px; }
  .masthead__clients {
    position: absolute;
    left: 242px; width: 574px; top: 270px;
    text-align: center;
    white-space: nowrap;
    font-family: "Nunito Sans", sans-serif;
    font-weight: 400;
    font-size: 30px;
    line-height: 1;
    color: var(--grey-text);
  }
  .specialties {
    position: absolute;
    left: 0; top: 358px;
    width: 961px; height: 574px;
    background: var(--teal);
    list-style: none;
    padding-top: 42px;
    text-align: center;
    color: var(--white);
    font-size: 40px;
    line-height: 60px;
    white-space: nowrap;
  }
  .contact {
    position: absolute;
    left: 0; top: 942px;
    width: 961px;
    text-align: center;
    color: var(--ink);
    font-style: normal;
    font-size: 31px;
    line-height: 47px;
    white-space: nowrap;
  }
  .contact__address { font-size: 40px; }
  .footer-band {
    position: absolute;
    left: 0; top: 1137px;
    width: 961px; height: 63px;
    background: var(--teal);
  }
  .footer-band__license {
    position: absolute;
    right: 20px; top: 16px;
    font-size: 27px;
    color: var(--white);
    white-space: nowrap;
  }
</style>
</head>
<body>
  <div class="ad">
    <div class="portrait" role="img" aria-label="Portrait photo of the therapist, smiling, with long brown hair"></div>

    <h1 class="masthead__name">DANA MORROW, MA, MFT</h1>
    <div class="masthead__rule"></div>
    <p class="masthead__service">Psychotherapy<small>for</small></p>
    <p class="masthead__clients">Individuals, Couples and Families</p>

    <ul class="specialties">
      <li>Parenting</li>
      <li>Depression</li>
      <li>Anxiety</li>
      <li>Life Transitions</li>
      <li>Divorce</li>
      <li>Couples Issues</li>
      <li>Women’s Issues</li>
      <li>Attachment and Neuroscience</li>
    </ul>

    <address class="contact">
      <div class="contact__address">148 Laurel Lane, Fairhaven, CA 94960</div>
      <div class="contact__web">www.danamorrow.com</div>
      <div class="contact__email">dana@danamorrow.com</div>
      <div class="contact__phone">415.555.0186</div>
    </address>

    <div class="footer-band">
      <span class="footer-band__license">License# MFC48203</span>
    </div>
  </div>
</body>
</html>
```